Book Cover - Steady Hand Choices

Hello. I am looking for a book cover for a book titled "Steady Hand Choices: Lessons Carried Up the Ridge and Into the Tower". I have included a basic design of what I am looking for. It should have a wildland firefighter climbing a hill on the left side and a business man with a briefcase climbing stairs on the right. I like the trees in the background from the timberline society logo but not too sure about the orange. I would like to have tree silhouettes in the background on the left and sky skyscrapers on the right that meet in the middle. I think where the two sides come together it should be intersected with an arrow to describe a path in decision making.

```html
<!DOCTYPE html>
<html lang="en">
<head>
<meta charset="utf-8">
<title>Steady Hand Choices – Book Cover</title>
<link rel="stylesheet" href="https://fonts.googleapis.com/css2?family=Marcellus&family=Poppins:wght@700&display=swap">
<style>
  :root {
    --page-bg: #ffffff;
    --cover-orange: #ff5a14;
    --cover-orange-light: #ff7a1a;
    --cover-orange-deep: #f2420a;
    --ink: #232323;
    --paper: #ffffff;
    --ember: #8a3a10;
  }
  * { margin: 0; padding: 0; box-sizing: border-box; }
  html, body {
    width: 1200px;
    height: 2686px;
    overflow: hidden;
    background: var(--page-bg);
  }
  .book-cover {
    position: absolute;
    left: 100px;
    top: 515px;
    width: 1000px;
    height: 1656px;
    background: linear-gradient(160deg, var(--cover-orange-deep) 0%, var(--cover-orange) 45%, var(--cover-orange-light) 100%);
    box-shadow: 0 10px 40px rgba(0,0,0,0.18);
    overflow: hidden;
  }
  .cover-frame {
    position: absolute;
    left: 23px;
    top: 23px;
    width: 951px;
    height: 1490px;
    border: 4px solid var(--paper);
    border-bottom: none;
  }
  .title {
    position: absolute;
    left: 0;
    width: 100%;
    text-align: center;
    font-family: "Marcellus", serif;
    font-size: 148px;
    line-height: 1;
    letter-spacing: 0.01em;
  }
  .title-line-1 { top: 105px; color: var(--paper); }
  .title-line-2 { top: 262px; color: var(--ink); }
  .title-line-3 { top: 415px; color: var(--paper); }
  .rule {
    position: absolute;
    left: 110px;
    width: 780px;
    height: 2px;
    background: rgba(255,255,255,0.85);
  }
  .rule-top { top: 616px; }
  .rule-bottom { top: 803px; }
  .subtitle {
    position: absolute;
    left: 0;
    top: 645px;
    width: 100%;
    text-align: center;
    font-family: "Marcellus", serif;
    font-size: 52px;
    line-height: 64px;
    color: var(--ink);
  }
  .cover-art {
    position: absolute;
    left: 0;
    top: 0;
    width: 1000px;
    height: 1656px;
  }
  .author-band {
    position: absolute;
    left: 0;
    top: 1536px;
    width: 100%;
    height: 120px;
    background: var(--paper);
    display: flex;
    align-items: center;
    justify-content: center;
    font-family: "Poppins", sans-serif;
    font-weight: 700;
    font-size: 42px;
    letter-spacing: 0.14em;
    color: var(--ink);
  }
</style>
</head>
<body>
  <div class="book-cover">
    <svg class="cover-art" viewBox="0 0 1000 1656" xmlns="http://www.w3.org/2000/svg">
      <defs>
        <linearGradient id="sceneTone" x1="0" y1="0" x2="0" y2="1">
          <stop offset="0" stop-color="#ff6a18" stop-opacity="0"/>
          <stop offset="0.35" stop-color="#8a3a10"/>
          <stop offset="0.7" stop-color="#232323"/>
          <stop offset="1" stop-color="#232323"/>
        </linearGradient>
      </defs>
      <rect class="scene-left" x="0" y="893" width="445" height="643" fill="url(#sceneTone)"
            role="img" aria-label="Silhouette of a wildland firefighter climbing a hill before pine trees"/>
      <rect class="scene-right" x="565" y="893" width="435" height="643" fill="url(#sceneTone)"
            role="img" aria-label="Silhouette of a businessman with a briefcase climbing stairs before city skyscrapers"/>
      <polygon class="path-arrow" fill="#ffffff"
               points="506,842 624,1037 565,1037 565,1536 445,1536 445,1037 384,1037"/>
    </svg>

    <div class="cover-frame"></div>

    <h1 class="title title-line-1">STEADY</h1>
    <div class="title title-line-2">HAND</div>
    <div class="title title-line-3">CHOICES</div>

    <div class="rule rule-top"></div>
    <p class="subtitle">LESSONS CARRIED UP THE RIDGE<br>AND INTO THE TOWER</p>
    <div class="rule rule-bottom"></div>

    <div class="author-band">MAREN L. WHITCOMBE</div>
  </div>
</body>
</html>
```